Brackenford Fluidworks needs a website describing the repair business we are in.

Brackenford Fluidworks is a full hydraulic repair facility. We have 2 shops. We repair and service all hydraulic cylinders, pneumatic cylinders, hydraulic pumps, motors, valves and gearboxes. Our services range from large industrial plants to the individual that owns one piece of equipment. We also offer removal and install of cylinders. Along with free pick up and delivery, within a certain distance which is usually 100 miles from one of our shops.

With over 30 years experience in the hydraulic business, we can repair or replace any job. There is not a job too big or too small, we service them all.

We have customers that send whole pieces of equipment to us to do complete overhauls on all the hydraulics. Ranging from a country club green roller to a 10 ton boom truck.

Target Market(s)

Industrial plants, road builders, dirt work companies, general contractors, owners of industrial equipment (bulldozers, excavators, loaders, scrapers, motor graders, etc.

Industry/Entity Type

Hydraulic

Number of Pages Required

5+ page

Font styles to use
Sans Serif

Colors
ec1f27
ffffff
aaaaaa

Requirements
Must have
• Information about what we offer and pictures of jobs completed.
Nice to have
• Nice stock photos of jobsites and industrial plants.
Should not have
• Any sort of comical characters.

```html
<!DOCTYPE html>
<html lang="en">
<head>
<meta charset="utf-8">
<title>Brackenford Fluidworks</title>
<link href="https://fonts.googleapis.com/css2?family=Poppins:wght@400;500;600&display=swap" rel="stylesheet">
<style>
:root{
  --red:#ec1f27;
  --red-dark:#c8161d;
  --white:#ffffff;
  --grey:#aaaaaa;
  --ink:#1e1e1e;
  --body:#333333;
  --line:#d9d9d9;
  --search:#ececec;
}
*{margin:0;padding:0;box-sizing:border-box}
html,body{width:1200px;height:2486px;overflow:hidden;background:var(--white)}
body{position:relative;font-family:"Poppins",sans-serif;color:var(--body)}
.abs{position:absolute}

.top-bar{left:0;top:0;width:1200px;height:5px;background:var(--red)}
.brand{display:flex;align-items:center;gap:10px}
.brand-mark{width:44px;height:44px;border-radius:50%;background:var(--red);flex:none}
.brand-name{font-weight:600;font-size:17px;line-height:1.15;color:var(--red);text-transform:uppercase}
.header-brand{left:161px;top:42px}

.search{left:641px;top:28px;width:242px;height:37px;border-radius:19px;background:var(--search);display:flex;align-items:center;justify-content:space-between;padding:0 16px 0 18px;font-size:12px;color:#555}
.quote-btn{left:891px;top:28px;width:146px;height:37px;border-radius:19px;background:var(--red);color:var(--white);font-size:12px;display:flex;align-items:center;justify-content:center;text-transform:uppercase}
.nav{top:92px;left:490px;font-size:13px;font-weight:500;color:var(--ink)}
.nav a{color:inherit;text-decoration:none;position:absolute;white-space:nowrap}
.nav a.active{color:var(--red)}

.hero{left:0;top:129px;width:1200px;height:497px;background:linear-gradient(160deg,#4a4540 0%,#34302c 40%,#26231f 70%,#3a3630 100%)}
.hero-title{left:0;top:303px;width:1200px;text-align:center;color:var(--white);font-size:32px;font-weight:600;text-transform:uppercase}
.hero-sub{left:0;top:358px;width:1200px;text-align:center;color:var(--white);font-size:14px;line-height:23px}
.hero-btn{left:500px;top:424px;width:199px;height:46px;border-radius:23px;background:var(--red);color:var(--white);font-size:14px;font-weight:500;display:flex;align-items:center;justify-content:center;text-transform:uppercase}
.hero-dot{left:1145px;width:14px;height:14px;border-radius:50%;background:var(--white)}
.hero-dot.on{left:1142px;width:19px;height:19px}

.card{top:666px;width:210px;height:320px;border-left:2px solid var(--line);padding-left:12px}
.card h3{font-size:16px;font-weight:500;color:var(--red);margin-bottom:9px;white-space:nowrap}
.card .pic{width:192px;height:152px;margin-left:2px}
.card p{font-size:11px;line-height:20px;margin:10px 0 0 5px;color:var(--body)}
.btn-sm{display:inline-flex;align-items:center;justify-content:center;width:87px;height:32px;background:var(--red);color:var(--white);font-size:11px;margin:13px 0 0 5px}

.divider{left:161px;top:1047px;width:876px;height:1px;background:var(--line)}
.about-title{left:161px;top:1084px;font-size:24px;font-weight:600;color:var(--red)}
.about-text{left:161px;top:1126px;width:565px;font-size:11px;line-height:21.5px;color:var(--ink)}
.about-text p{margin-bottom:10px}
.about-pic{left:737px;top:1105px;width:300px;height:231px;background:linear-gradient(135deg,#7b7266,#a48a5c 45%,#c9a93f 60%,#5d574e)}

.band{left:0;top:1402px;width:1200px;height:343px;background:radial-gradient(ellipse at 30% 40%,#555 0%,#3c3c3c 55%,#2f2f2f 100%)}
.band-title{left:0;top:1458px;width:1200px;text-align:center;color:var(--white);font-size:24px;font-weight:500;text-transform:uppercase}
.service{top:1516px;width:170px;text-align:center;color:var(--white);font-size:17px;line-height:24px}
.service .circle{width:129px;height:129px;border-radius:50%;background:var(--red);margin:0 auto 12px;display:flex;align-items:center;justify-content:center}

.news-title{left:0;top:1782px;width:1200px;text-align:center;font-size:24px;font-weight:500;color:var(--ink);text-transform:uppercase}
.news{top:1848px;width:280px}
.news .pic{position:relative;width:280px;height:145px}
.date{position:absolute;left:0;bottom:0;width:45px;height:45px;background:var(--red);color:var(--white);text-align:center;font-size:9px;line-height:11px;padding-top:8px;text-transform:uppercase}
.date b{display:block;font-size:15px;font-weight:500;line-height:18px}
.news h4{font-size:16px;font-weight:600;color:var(--ink);margin-top:17px}
.news p{font-size:11px;line-height:21.5px;margin-top:8px;color:var(--ink);width:255px}

.footer{left:0;top:2161px;width:1200px;height:270px;background:var(--red);color:var(--white)}
.footer-brand{left:161px;top:2220px;flex-direction:column;gap:10px;text-align:center;width:168px}
.footer-brand .brand-mark{width:70px;height:70px;background:var(--white)}
.footer-brand .brand-name{color:var(--white);font-size:20px}
.f-head{font-size:17px;font-weight:400}
.f-col{top:2205px;font-size:11px;line-height:26px;color:var(--white)}
.newsletter p{line-height:21px;margin-top:14px;width:170px}
.email-field{width:165px;border-bottom:2px solid var(--white);font-size:11px;font-style:italic;padding-bottom:4px;margin-top:22px}
.signup{margin-top:16px;width:100px;height:36px;border-radius:18px;background:#2a2a2a;display:flex;align-items:center;justify-content:center;font-size:12px;text-transform:uppercase}
.links ul{list-style:none;margin-top:10px}
.contact ul{list-style:none;margin-top:12px;line-height:22px}
.contact li{display:flex;gap:8px;align-items:flex-start}
.contact svg{flex:none;margin-top:6px}
.socials{display:flex;gap:10px;margin-top:16px}
.socials span{width:30px;height:30px;border:1.5px solid var(--white);border-radius:50%}
.legal{left:0;top:2431px;width:1200px;height:55px;background:var(--red-dark);color:var(--white);font-size:11px;display:flex;align-items:center;justify-content:center}
</style>
</head>
<body>
<div class="abs top-bar"></div>

<div class="abs brand header-brand"><span class="brand-mark"></span><span class="brand-name">Brackenford<br>Fluidworks</span></div>
<div class="abs search"><span>Search</span>
<svg width="13" height="13" viewBox="0 0 13 13"><circle cx="5.5" cy="5.5" r="4" fill="none" stroke="#333" stroke-width="1.8"/><line x1="8.5" y1="8.5" x2="12" y2="12" stroke="#333" stroke-width="1.8"/></svg></div>
<div class="abs quote-btn">Request a Quote</div>
<nav class="abs nav">
  <a class="active" style="left:0">HOME</a>
  <a style="left:83px">ABOUT US</a>
  <a style="left:196px">SERVICE &amp; REPAIR</a>
  <a style="left:360px">PRODUCTS</a>
  <a style="left:479px">CONTACT</a>
</nav>

<div class="abs hero" role="img" aria-label="Hydraulic cylinders strapped on a flatbed trailer outside the shop"></div>
<h1 class="abs hero-title">Brackenford Fluidworks</h1>
<p class="abs hero-sub">Sed ut perspiciatis unde omnis iste natus sit volup tatem accu<br>svSed ut perspiciati nis iste natus sit volup tamn.</p>
<div class="abs hero-btn">Get Started Here</div>
<span class="abs hero-dot" style="top:373px"></span>
<span class="abs hero-dot on" style="top:394px"></span>
<span class="abs hero-dot" style="top:420px"></span>

<div class="abs card" style="left:161px">
  <h3>Hydraulics Repair</h3>
  <div class="pic" role="img" aria-label="Orange cylinder on a pallet in the repair shop" style="background:linear-gradient(180deg,#3b352f,#b8896a 45%,#d9521f 65%,#8a5a3a)"></div>
  <p>Sed ut perspiciatis unde omniste natus error sit voluptatem accusn tium doloremque laudantium, to tam rem aperiam, eaque.</p>
  <span class="btn-sm">Read More</span>
</div>
<div class="abs card" style="left:384px">
  <h3>Hydraulics Service</h3>
  <div class="pic" role="img" aria-label="Close-up of a yellow hydraulic cylinder" style="background:linear-gradient(135deg,#3a3733,#d8b51e 40%,#f0d22c 55%,#4a463e)"></div>
  <p>Sed ut perspiciatis unde omniste natus error sit voluptatem accusn tium doloremque laudantium, to tam rem aperiam, eaque.</p>
  <span class="btn-sm">Read More</span>
</div>
<div class="abs card" style="left:608px">
  <h3>Who We Are</h3>
  <div class="pic" role="img" aria-label="Rebuilt cylinder rods laid on a wooden pallet" style="background:linear-gradient(180deg,#6d6a66,#9c9790 40%,#b89a6b 70%,#7d6a4f)"></div>
  <p>Sed ut perspiciatis unde omniste natus error sit voluptatem accusn tium doloremque laudantium, to tam rem aperiam, eaque.</p>
  <span class="btn-sm">Read More</span>
</div>
<div class="abs card" style="left:829px">
  <h3>Equipments</h3>
  <div class="pic" role="img" aria-label="Black hydraulic cylinders lined up on a bench" style="background:linear-gradient(180deg,#8f8e8c,#2a2a2a 45%,#555 65%,#9a9894)"></div>
  <p>Sed ut perspiciatis unde omniste natus error sit voluptatem accusn tium doloremque laudantium, to tam rem aperiam, eaque.</p>
  <span class="btn-sm">Read More</span>
</div>

<div class="abs divider"></div>

<h2 class="abs about-title">ABOUT US</h2>
<div class="abs about-text">
  <p>Brackenford Fluidworks is a full hydraulic repair facility. We have 2 shops. We repair and service all hydraulic cylinders, pneumatic cylinders, hydraulic pumps, motors, valves and gearboxes. Our services range from large industrial plants to the individual that owns one piece of equipment. We also offer removal and install of cylinders. Along with free pick up and delivery, within a certain distance which is usually 100 miles from one of our shops.</p>
  <p>With over 30 years experience in the hydraulic business, we can repair or replace any job. There is not a job too big or too small, we service them all.</p>
  <p>We have customers that send whole pieces of equipment to us to do complete overhauls on all the hydraulics. Ranging from a country club green roller to a 10 ton boom truck.</p>
</div>
<div class="abs about-pic" role="img" aria-label="Yellow and black cylinders on pallets after repair"></div>

<div class="abs band" role="img" aria-label="Darkened shop floor with machinery in the background"></div>
<h2 class="abs band-title">What We Do</h2>

<div class="abs service" style="left:167px">
  <div class="circle"><svg width="70" height="30" viewBox="0 0 70 30" fill="#fff"><rect x="2" y="4" width="40" height="22" rx="3"/><rect x="42" y="12" width="22" height="6"/><rect x="62" y="8" width="6" height="14" rx="1"/></svg></div>
  Hydraulic<br>Cylinders
</div>
<div class="abs service" style="left:338px">
  <div class="circle"><svg width="64" height="48" viewBox="0 0 64 48" fill="none" stroke="#fff" stroke-width="4" stroke-linecap="round"><path d="M4 10 H40 A7 7 0 1 0 33 3"/><path d="M4 24 H54 A7 7 0 1 1 47 31"/><path d="M4 38 H30"/></svg></div>
  Pneumatic<br>Cylinders
</div>
<div class="abs service" style="left:508px">
  <div class="circle"><svg width="60" height="60" viewBox="0 0 60 60" fill="none" stroke="#fff" stroke-width="4"><circle cx="30" cy="30" r="24"/><path d="M20 30 H40 M33 23 L40 30 L33 37" stroke-linecap="round" stroke-linejoin="round"/></svg></div>
  Hydraulic<br>Pumps
</div>
<div class="abs service" style="left:679px">
  <div class="circle"><svg width="60" height="60" viewBox="0 0 60 60" fill="#fff"><g transform="translate(30 30)"><rect x="-5" y="-28" width="10" height="56"/><rect x="-5" y="-28" width="10" height="56" transform="rotate(45)"/><rect x="-5" y="-28" width="10" height="56" transform="rotate(90)"/><rect x="-5" y="-28" width="10" height="56" transform="rotate(135)"/><circle r="20"/><circle r="8" fill="#ec1f27"/></g></svg></div>
  Motors
</div>
<div class="abs service" style="left:850px">
  <div class="circle"><svg width="60" height="60" viewBox="0 0 60 60" fill="none" stroke="#fff" stroke-width="4" stroke-linejoin="round"><path d="M6 18 L30 30 L6 42 Z M54 18 L30 30 L54 42 Z"/><line x1="30" y1="30" x2="30" y2="8"/><line x1="20" y1="8" x2="40" y2="8" stroke-linecap="round"/></svg></div>
  Valves and<br>Gearboxes
</div>

<h2 class="abs news-title">Latest News</h2>
<article class="abs news" style="left:161px">
  <div class="pic" role="img" aria-label="Cylinders laid across a steel workbench" style="background:linear-gradient(180deg,#2d2d2d,#6a6866 40%,#b5b3ae 70%,#555)"><span class="date">Mar<b>05</b></span></div>
  <h4>Finibus Bonorum eMalor</h4>
  <p>Lorem ipsum dolor sit ans ectetur adipisicin elit, sed doeiusmod tempor incididuntaborem ipsum dolor sit amons ectetur adipis.</p>
</article>
<article class="abs news" style="left:459px">
  <div class="pic" role="img" aria-label="Red cylinders stacked on wooden pallets" style="background:linear-gradient(180deg,#4a4540,#8f3a30 40%,#b98f60 75%,#6b5b48)"><span class="date">Mar<b>04</b></span></div>
  <h4>Finibus Bonorum eMalor</h4>
  <p>Lorem ipsum dolor sit ans ectetur adipisicin elit, sed doeiusmod tempor incididuntaborem ipsum dolor sit amons ectetur adipis.</p>
</article>
<article class="abs news" style="left:757px">
  <div class="pic" role="img" aria-label="Blue hydraulic pump and yellow cylinders on a pallet" style="background:linear-gradient(135deg,#6e675c,#c9a25a 40%,#2e4f8c 60%,#d6b53a 80%,#7a6e58)"><span class="date">Mar<b>02</b></span></div>
  <h4>Finibus Bonorum eMalor</h4>
  <p>Lorem ipsum dolor sit ans ectetur adipisicin elit, sed doeiusmod tempor incididuntaborem ipsum dolor sit amons ectetur adipis.</p>
</article>

<footer class="abs footer"></footer>
<div class="abs brand footer-brand"><span class="brand-mark"></span><span class="brand-name">Brackenford<br>Fluidworks</span></div>

<div class="abs f-col newsletter" style="left:421px">
  <div class="f-head">Newsletter</div>
  <p>Subscribe to us to get and receive the latest news, sales and updates.</p>
  <div class="email-field">Email Address:</div>
  <div class="signup">Sign Up</div>
</div>
<div class="abs f-col links" style="left:676px">
  <div class="f-head">Links</div>
  <ul><li>About Us</li><li>Service &amp; Repair</li><li>Products</li><li>Locations</li><li>News</li></ul>
</div>
<div class="abs f-col contact" style="left:838px">
  <div class="f-head">Contact</div>
  <ul>
    <li><svg width="9" height="12" viewBox="0 0 9 12" fill="#fff"><path d="M4.5 0 A4.5 4.5 0 0 1 9 4.5 C9 8 4.5 12 4.5 12 C4.5 12 0 8 0 4.5 A4.5 4.5 0 0 1 4.5 0 Z"/><circle cx="4.5" cy="4.5" r="1.6" fill="#ec1f27"/></svg><span>45 Lorem isupm dore, Siuite 2000<br>NEW YORK, lorem isum dolr 2353</span></li>
    <li><svg width="10" height="10" viewBox="0 0 10 10" fill="#fff"><path d="M2 0 L4 2.5 L3 4 Q4.5 6 6 7 L7.5 6 L10 8 L8.5 10 Q3 9.5 0 2 Z"/></svg><span>Phone: (555) 014-2290</span></li>
    <li><svg width="11" height="8" viewBox="0 0 11 8" fill="#fff"><rect width="11" height="8"/><path d="M0 0 L5.5 4.5 L11 0" fill="none" stroke="#ec1f27" stroke-width="1"/></svg><span>info@brackenford.example</span></li>
  </ul>
  <div class="socials"><span></span><span></span><span></span><span></span></div>
</div>

<div class="abs legal">© 2018 Brackenford Fluidworks. All rights are reserved. Privacy | Terms of use</div>
</body>
</html>
```